Bram Keystone Homes needs a business card

We need a business card for a new company in Canada, Ontario. Our company is all about luxury contraction homes for our clients. Our product and services are custom projects design. Under the business logo that will be created, we want a slogan that will be a memorable phrase for consumers to remember us to tell their friends and relatives.

Additional infomation
- Ludovic Entrasse
- President / Ceo
-519.604.3087

Find point what luxury construction products and services can be done

We like to see colors:
- #663300
- and something other colors or color that would attract the client needs and wants

The final design should communicate leads from new or old clients that will grow our empire. Most of all, we try to work among the budget that clients want

NOTE
- we also need an icon for the business (Example: Instagram, Facebook, and Whatsapp icons)
- We want the company name to be remembered easily for clients and our distributors who would get our orders.
- we need an icon on the business cards: Facebook and Instagram.

Thanks,
Bram Keystone Homes

```html
<!DOCTYPE html>
<html lang="en">
<head>
<meta charset="utf-8">
<title>Bram Keystone Homes — Business Card</title>
<link href="https://fonts.googleapis.com/css2?family=Work+Sans:wght@400;500;700;800&display=swap" rel="stylesheet">
<style>
  :root {
    --brand-brown: #663300;
    --card-white: #ffffff;
    --backdrop: #a9a9a9;
    --backdrop-light: #cfcfcf;
    --card-shadow: rgba(0, 0, 0, 0.28);
  }
  * { box-sizing: border-box; margin: 0; padding: 0; }
  html, body { width: 1200px; height: 930px; overflow: hidden; }
  body {
    position: relative;
    background: radial-gradient(ellipse at 50% 45%, var(--backdrop-light), var(--backdrop));
    font-family: "Work Sans", Arial, sans-serif;
  }
  .card {
    position: absolute;
    width: 540px;
    height: 310px;
    border-radius: 22px;
    overflow: hidden;
    box-shadow: 0 10px 24px var(--card-shadow);
  }
  .brand-name {
    font-weight: 800;
    line-height: 1;
    white-space: nowrap;
  }
  .brand-tagline {
    font-weight: 500;
    letter-spacing: 0.3px;
    text-transform: uppercase;
    white-space: nowrap;
  }

  /* Front */
  .card--front {
    left: 70px; top: 130px;
    background: var(--brand-brown);
    display: flex; flex-direction: column; align-items: center; justify-content: center;
    color: var(--card-white);
  }
  .card--front .brand-name { font-size: 34px; }
  .card--front .brand-tagline { font-size: 13px; margin-top: 8px; }

  /* Back */
  .card--back {
    left: 590px; top: 490px;
    background: var(--brand-brown);
  }
  .card__sweep { position: absolute; inset: 0; width: 100%; height: 100%; }
  .back-brand {
    position: absolute;
    right: 22px; top: 44px;
    width: 310px;
    text-align: center;
    color: var(--brand-brown);
  }
  .back-brand .brand-name { font-size: 26px; }
  .back-brand .brand-tagline { font-size: 9.5px; margin-top: 6px; }

  .contact {
    position: absolute;
    left: 34px; bottom: 22px;
    color: var(--card-white);
    font-size: 12.5px;
    line-height: 1.3;
  }
  .contact__name { font-weight: 700; font-size: 17px; }
  .contact__title { margin-bottom: 9px; }
  .contact__address { margin-bottom: 7px; }
  .contact__line { display: flex; align-items: center; gap: 8px; }
  .contact__line svg { width: 10px; height: 10px; flex: none; }
</style>
</head>
<body>

  <section class="card card--front" aria-label="Card front">
    <div class="brand-name">Bram Keystone Homes</div>
    <div class="brand-tagline">- Home Renovations - Custom Project Design -</div>
  </section>

  <section class="card card--back" aria-label="Card back">
    <svg class="card__sweep" viewBox="0 0 540 310" preserveAspectRatio="none" aria-hidden="true">
      <path d="M118 0 C 160 160 340 232 540 222" fill="none" stroke="#ffffff" stroke-width="3"/>
      <path d="M140 0 C 180 140 330 205 540 195 L540 0 Z" fill="#ffffff"/>
    </svg>

    <div class="back-brand">
      <div class="brand-name">Bram Keystone Homes</div>
      <div class="brand-tagline">- Home Renovations - Custom Project Design -</div>
    </div>

    <div class="contact">
      <div class="contact__name">Ludovic Entrasse</div>
      <div class="contact__title">President / Ceo</div>
      <div class="contact__address">1184 Maplewood Avenue<br>Guelph, ON N1H 3K2</div>
      <div class="contact__line">
        <svg viewBox="0 0 12 12" aria-hidden="true"><path d="M2.5 1 L4.5 1 L5.2 3.6 L4 4.6 C4.7 6 6 7.3 7.4 8 L8.4 6.8 L11 7.5 L11 9.5 C11 10.3 10.3 11 9.5 11 C5 11 1 7 1 2.5 C1 1.7 1.7 1 2.5 1 Z" fill="#ffffff"/></svg>
        <span>519.604.3087</span>
      </div>
      <div class="contact__line">
        <svg viewBox="0 0 12 12" aria-hidden="true"><rect x="1" y="2.5" width="10" height="7" fill="none" stroke="#ffffff" stroke-width="1.2"/><path d="M1 2.5 L6 6.5 L11 2.5" fill="none" stroke="#ffffff" stroke-width="1.2"/></svg>
        <span>info@bramkeystone.com</span>
      </div>
      <div class="contact__line">
        <svg viewBox="0 0 12 12" aria-hidden="true"><circle cx="6" cy="6" r="5" fill="none" stroke="#ffffff" stroke-width="1.1"/><ellipse cx="6" cy="6" rx="2.2" ry="5" fill="none" stroke="#ffffff" stroke-width="1"/><path d="M1 6 H11" stroke="#ffffff" stroke-width="1"/></svg>
        <span>www.bramkeystone.com</span>
      </div>
    </div>
  </section>

</body>
</html>
```